Redesign of Form/Document Navigation Page

I need a redesign of our document and navigation bar on the left. We want the same navigation bar layout/setup but want the buttons and typography to be simple and matching all over. The form needs to be aesthetically pleasing and fit within the page.

1st attachment is our Direct Deposit and the second is the form continued.

```html
<!DOCTYPE html>
<html lang="en">
<head>
<meta charset="utf-8">
<title>Sentryline Security – Direct Deposit</title>
<link href="https://fonts.googleapis.com/css2?family=Open+Sans:wght@400;600;700&family=Montserrat:wght@400;500;600&display=swap" rel="stylesheet">
<style>
  :root{
    --navy:#23599a;
    --navy-dark:#1f4f8a;
    --gold:#ecb21f;
    --page:#f2f2f2;
    --white:#ffffff;
    --text:#222222;
    --muted:#555555;
    --line:#d4d4d4;
    --field-border:#cfcfcf;
    --panel-grey:#f1f1f1;
    --ui-font:"Montserrat",Arial,sans-serif;
    --body-font:"Open Sans",Arial,sans-serif;
  }
  *{box-sizing:border-box;margin:0;padding:0}
  html,body{width:1200px;height:1028px;overflow:hidden}
  body{background:var(--page);font-family:var(--body-font);color:var(--text);position:relative}

  .site-header{position:absolute;left:0;top:0;width:1200px;height:75px;background:var(--white);border-bottom:1px solid #e2e2e2}
  .brand{position:absolute;left:66px;top:22px;display:flex;align-items:center;gap:8px}
  .brand-mark{width:28px;height:28px;background:var(--navy);border-radius:50%}
  .brand-name{font-family:var(--body-font);font-weight:700;font-size:14px;line-height:15px;color:var(--gold);text-transform:uppercase;width:130px}
  .main-nav{position:absolute;left:291px;top:29px;display:flex;gap:16px;font-family:var(--ui-font);font-size:13px;color:#333}
  .user-area{position:absolute;left:1024px;top:18px;height:38px;border-left:1px solid #e2e2e2;display:flex;align-items:center;padding-left:21px;gap:10px;font-size:10px;color:#444}
  .user-area .caret{color:#aaa;font-size:7px}
  .power{width:27px;height:27px;border-radius:50%;border:1px solid #ccc;display:flex;align-items:center;justify-content:center}

  .back-btn{position:absolute;left:63px;top:90px;width:113px;height:28px;background:var(--navy);color:#fff;font-family:var(--ui-font);font-size:10px;font-weight:500;display:flex;align-items:center;justify-content:center;letter-spacing:.2px}

  .side-nav{position:absolute;left:63px;top:134px}
  .nav-card{position:absolute;left:0;width:229px;height:107px;background:var(--white);border:2px solid #e4e4e4;border-left:none}
  .nav-card::before{content:"";position:absolute;left:0;top:-2px;bottom:-2px;width:47px;background:var(--gold)}
  .nav-icon{position:absolute;left:13px;top:20px;width:63px;height:63px;border-radius:50%;background:var(--navy);border:2px solid #fff;box-shadow:0 0 0 1px #d9d9d9}
  .nav-label{position:absolute;left:83px;right:6px;top:50%;transform:translateY(-50%);font-family:var(--ui-font);font-size:13px;line-height:18px;color:#444;white-space:nowrap}

  .doc-panel{position:absolute;left:315px;top:134px;width:818px;height:800px;background:var(--white);border:1px solid var(--line);overflow:hidden}
  .scrollbar{position:absolute;right:0;top:0;width:11px;height:100%;background:#f4f4f4;border-left:1px solid #e6e6e6}
  .scrollbar .thumb{position:absolute;left:2px;top:10px;width:7px;height:196px;background:#c6c6c6}
  .doc-title{position:absolute;left:24px;top:26px;font-size:12.5px;font-weight:600}
  .doc-body{position:absolute;left:24px;top:56px;width:760px;font-size:9.5px;line-height:20.6px;color:#333}
  .doc-body p+p{margin-top:12px}
  .emp-name{position:absolute;left:23px;top:209px;font-size:12px;font-weight:600}
  .sig-label{position:absolute;left:23px;top:232px;font-size:11px;color:#333}
  .sig-line{position:absolute;left:23px;top:264px;width:246px;border-top:2px solid #ddd}
  .date-label{position:absolute;left:284px;top:258px;font-size:9.5px;color:#444}
  .field{position:absolute;border:1px solid var(--field-border);background:#fff}
  .sig-pad{position:absolute;left:23px;top:325px;width:251px;height:90px;border:1px solid var(--field-border)}
  .sig-pad::after{content:"";position:absolute;left:0;right:0;top:51px;border-top:2px solid #e1e1e1}
  .accept-btn{position:absolute;left:23px;top:437px;width:161px;height:34px;background:var(--gold);color:#fff;font-family:var(--ui-font);font-size:11.5px;font-weight:500;display:flex;align-items:center;justify-content:center;letter-spacing:.3px}

  .manager-heading{position:absolute;left:0;width:806px;top:525px;text-align:center;font-family:var(--ui-font);font-size:17.5px;font-weight:500;color:var(--navy-dark)}
  .manager-box{position:absolute;left:23px;top:570px;width:772px;height:182px;background:var(--panel-grey);border:1px solid #d6d6d6}
  .mgr-label{position:absolute;font-size:10px;color:#555}

  .site-footer{position:absolute;left:66px;top:965px;width:1068px;border-top:1px solid #e0e0e0}
  .footer-links{position:absolute;left:0;top:26px;font-size:9.8px;color:#333;display:flex;gap:9px;white-space:nowrap}
  .social{position:absolute;left:957px;top:20px;display:flex;gap:4px}
  .social span{width:25px;height:25px;border-radius:50%}
</style>
</head>
<body>
<header class="site-header">
  <div class="brand"><span class="brand-mark"></span><span class="brand-name">Sentryline Security</span></div>
  <nav class="main-nav"><span>HOME</span><span>HELP</span></nav>
  <div class="user-area"><span>SLS Admin <span class="caret">▼</span></span>
    <span class="power"><svg width="12" height="12" viewBox="0 0 12 12"><path d="M3.6 3.2a4 4 0 1 0 4.8 0" fill="none" stroke="#23599a" stroke-width="1.6" stroke-linecap="round"/><line x1="6" y1="1" x2="6" y2="5.5" stroke="#23599a" stroke-width="1.6" stroke-linecap="round"/></svg></span>
  </div>
</header>

<div class="back-btn">BACK TO PROFILE</div>

<nav class="side-nav">
  <div class="nav-card" style="top:0"><span class="nav-icon" role="img" aria-label="Direct deposit icon"></span><span class="nav-label">Direct Deposit</span></div>
  <div class="nav-card" style="top:115px"><span class="nav-icon" role="img" aria-label="Change W-4 icon"></span><span class="nav-label">Change W-4</span></div>
  <div class="nav-card" style="top:230px"><span class="nav-icon" role="img" aria-label="Labour code icon"></span><span class="nav-label">Labour Code</span></div>
  <div class="nav-card" style="top:346px"><span class="nav-icon" role="img" aria-label="Personal information icon"></span><span class="nav-label">Personal Information</span></div>
  <div class="nav-card" style="top:461px"><span class="nav-icon" role="img" aria-label="Appraisal and review icon"></span><span class="nav-label">Appraisal<br>and Review</span></div>
  <div class="nav-card" style="top:576px"><span class="nav-icon" role="img" aria-label="Write up-slip icon"></span><span class="nav-label">Write Up-Slip</span></div>
  <div class="nav-card" style="top:691px"><span class="nav-icon" role="img" aria-label="Employee performance icon"></span><span class="nav-label">Employee<br>Performance</span></div>
</nav>

<main class="doc-panel">
  <div class="scrollbar"><span class="thumb"></span></div>
  <h1 class="doc-title">IMPORTANT! Please read and sign before completing and submitting.</h1>
  <div class="doc-body">
    <p>I hereby authorize SENTRYLINE SECURITY to deposit any amounts owed me, as instructed by my employer, by initiating credit entries to my account at the financial institution (hereinafter "Bank") indicated on this form. Further. I authorize Bank to accept and to credit any credit entries indicated by SENTRYLINE SECURITY to my account. In the even that SENTRYLINE SECURITY deposits funds erroneously into my account. I authorize SENTRYLINE SECURITY to debit my account for an amount not to exceed the original amount of the erroneous credit.</p>
    <p>This authorization is to remain in full force and effect until SENTRYLINE SECURITY and Bank have received written notice from me of its termination in such time and in such manner as to afford SENTRYLINE SECURITY and Bank reasonable opportunity to act on it.</p>
  </div>
  <div class="emp-name">EMPLOYEE NAME: .</div>
  <div class="sig-label">Employee Signature</div>
  <div class="sig-line"></div>
  <div class="date-label">Sign Date</div>
  <div class="field" style="left:23px;top:279px;width:251px;height:31px"></div>
  <div class="field" style="left:284px;top:279px;width:251px;height:31px"></div>
  <div class="sig-pad"></div>
  <div class="accept-btn">ACCEPT DOCUMENT</div>

  <h2 class="manager-heading">ONLY PAYROLL MANAGER SIGNS BELOW</h2>
  <section class="manager-box">
    <span class="mgr-label" style="left:12px;top:26px">Company Name:</span>
    <div class="field" style="left:13px;top:44px;width:361px;height:35px"></div>
    <span class="mgr-label" style="left:12px;top:92px">Employee File Number:</span>
    <div class="field" style="left:13px;top:109px;width:361px;height:35px"></div>
    <span class="mgr-label" style="left:389px;top:26px">Comments:</span>
    <div class="field" style="left:389px;top:44px;width:361px;height:100px"></div>
  </section>
</main>

<footer class="site-footer">
  <div class="footer-links"><span>© 2016 All Copyrights are Reserved. Terms of Use</span><span>Privacy Policy</span><span>Sitemap</span><span>Contact Us</span></div>
  <div class="social">
    <span style="background:#3fa9de"></span><span style="background:#2d5a9a"></span><span style="background:#1f6fa6"></span><span style="background:#d9412f"></span>
  </div>
</footer>
</body>
</html>
```